Maplecrest Disability - Social Security Disability Attorneys

Our company is expanding to attract clients nationwide for our social security disability practice. We have a logo, but I am looking for a creative and elegant letterhead that projects an image of being technologically advanced but still professional enough for the legal field. I am looking for the "wow factor" combined with this is still professional enough for a law practice.

Requesting letterhead and business card design
Updates

Had to update and change the logo. The previous logo had a typo. Please send updates with the new logo for consideration. The letterhead and business cards should be professional enough to be used for a law firm. Thanks.

Industry/Entity Type

Law Practice, Law Firm, Healthcare Industry, Government

Colors

Designer to choose colors to be used in the design.

Requirements
Nice to have
• **Please create a vertical design for the business card**

```html
<!DOCTYPE html>
<html lang="en">
<head>
<meta charset="utf-8">
<title>Maplecrest Disability – Business Card</title>
<link href="https://fonts.googleapis.com/css2?family=Montserrat:wght@400;500;600;800&display=swap" rel="stylesheet">
<style>
  :root {
    --canvas: #e9eaee;
    --card-white: #ffffff;
    --brand-blue: #506cb8;
    --brand-blue-deep: #4a63a8;
    --brand-blue-light: #5f79c0;
    --accent-orange: #f47f20;
    --ink: #151515;
    --on-blue: #ffffff;
  }
  * { box-sizing: border-box; margin: 0; padding: 0; }
  html, body { width: 1200px; height: 1200px; overflow: hidden; }
  body {
    background: var(--canvas);
    font-family: "Montserrat", Arial, sans-serif;
    display: flex;
    align-items: center;
    justify-content: center;
    gap: 80px;
  }
  .card {
    position: relative;
    width: 400px;
    height: 700px;
    border-radius: 34px;
    overflow: hidden;
    box-shadow: 0 12px 30px rgba(0,0,0,0.18);
  }

  /* Front */
  .card-front { background: var(--card-white); color: var(--ink); text-align: center; }
  .brand { padding-top: 110px; }
  .brand-name {
    display: inline-flex; align-items: center; gap: 10px;
    font-size: 27px; font-weight: 600; letter-spacing: 1.5px;
    text-transform: uppercase; color: var(--brand-blue);
  }
  .brand-dot { width: 12px; height: 12px; border-radius: 50%; background: var(--accent-orange); }
  .brand-tagline {
    margin-top: 6px; font-size: 9.5px; font-weight: 500;
    letter-spacing: 2.2px; text-transform: uppercase; color: var(--brand-blue);
  }
  .person { margin-top: 62px; }
  .person-name {
    font-size: 27px; font-weight: 800; text-transform: uppercase;
    color: var(--accent-orange); letter-spacing: 0.5px;
  }
  .person-role {
    display: flex; align-items: center; justify-content: center; gap: 8px;
    margin-top: 2px; font-size: 19px; font-weight: 500;
  }
  .person-role::before, .person-role::after {
    content: ""; width: 72px; height: 2px; background: var(--accent-orange);
  }
  .address { margin-top: 38px; font-size: 18px; line-height: 1.35; font-weight: 500; }
  .contact-icons {
    display: flex; justify-content: center; gap: 46px; margin-top: 30px;
  }
  .contact-icons svg { width: 22px; height: 22px; fill: var(--accent-orange); }
  .contact-lines { margin-top: 22px; font-size: 17px; line-height: 1.5; font-weight: 500; }
  .front-band { position: absolute; left: 0; bottom: 0; width: 400px; height: 170px; }

  /* Back */
  .card-back {
    background: linear-gradient(160deg, var(--brand-blue-deep) 0%, var(--brand-blue) 50%, var(--brand-blue-light) 100%);
    color: var(--on-blue); text-align: center;
  }
  .back-texture {
    position: absolute; inset: 0;
    background: linear-gradient(115deg, rgba(255,255,255,0) 40%, rgba(255,255,255,0.06) 60%, rgba(255,255,255,0) 80%);
  }
  .card-back .brand { position: relative; padding-top: 190px; }
  .card-back .brand-name, .card-back .brand-tagline { color: var(--on-blue); }
  .industries {
    position: absolute; left: 0; right: 0; bottom: 70px;
    font-size: 17px; font-weight: 500; line-height: 1.45;
  }
</style>
</head>
<body>
  <article class="card card-front">
    <header class="brand">
      <div class="brand-name"><span class="brand-dot"></span>Maplecrest Disability</div>
      <div class="brand-tagline">Social Security Disability Attorneys</div>
    </header>
    <section class="person">
      <h1 class="person-name">Dana Whitfield</h1>
      <p class="person-role">Co-Founder</p>
    </section>
    <p class="address">Suite 4, Level 12, Harbor<br>Street Easton NSW 2100</p>
    <div class="contact-icons">
      <svg viewBox="0 0 24 24" aria-label="Phone"><path d="M6.6 10.8a15.1 15.1 0 0 0 6.6 6.6l2.2-2.2a1 1 0 0 1 1-.25 11.4 11.4 0 0 0 3.6.57 1 1 0 0 1 1 1V20a1 1 0 0 1-1 1A17 17 0 0 1 3 4a1 1 0 0 1 1-1h3.5a1 1 0 0 1 1 1c0 1.25.2 2.45.57 3.57a1 1 0 0 1-.25 1z"/></svg>
      <svg viewBox="0 0 24 24" aria-label="Email"><path d="M2 5h20v14H2z M2 5l10 8 10-8" stroke="#fff" stroke-width="1.4"/></svg>
      <svg viewBox="0 0 24 24" aria-label="Website"><circle cx="12" cy="12" r="10"/><path d="M2 12h20M12 2c3 3 3 17 0 20M12 2c-3 3-3 17 0 20" stroke="#fff" stroke-width="1.2" fill="none"/></svg>
    </div>
    <div class="contact-lines">
      <p>555-014-2290</p>
      <p>info@maplecrestdisability.com</p>
      <p>www.maplecrestdisability.com</p>
    </div>
    <svg class="front-band" viewBox="0 0 400 170" preserveAspectRatio="none">
      <path d="M0 20 C110 120 270 150 400 110 L400 170 L0 170 Z" fill="var(--brand-blue)"/>
      <path d="M40 28 C140 110 250 130 340 122" stroke="var(--accent-orange)" stroke-width="4" fill="none" stroke-linecap="round"/>
    </svg>
  </article>

  <article class="card card-back">
    <div class="back-texture" role="img" aria-label="Faint overlapping geometric light panels across the blue background"></div>
    <header class="brand">
      <div class="brand-name"><span class="brand-dot"></span>Maplecrest Disability</div>
      <div class="brand-tagline">Social Security Disability Attorneys</div>
    </header>
    <p class="industries">Law Practice, Law Firm,<br>Healthcare Industry, Government</p>
  </article>
</body>
</html>
```